Business card for my new company (Accounting firm)

I need a business card for my new business Brightwell Advisory and Ledger SA. Our services are accounting, tax, audit and financial management. Our customers are small companies, start-ups and new companies. The final design has to show financial security, trust and growth. Please find our logo attached to the business card. Text for the business card: Brightwell Advisory and Ledger SA Tomas Varenholt Director and Founder Certified Accountant Tel. 022 418 57 34 tv@clairevalconseil.ch www.clairevalconseil.ch Rue des Vergières 27 1201 Geneva
Target Market(s)
Our customers are small companies, start-ups and new companies.
Industry/Entity Type
Finance And Accounting
Contact Information for Business Card
Claireval Conseil et Comptes SA
Tomas Varenholt
Directeur et Fondateur
Expert-comptable diplômé
Tél. 022 418 57 34
tv@clairevalconseil.ch
www.clairevalconseil.ch
Rue des Vergières 27
1201 Genève

```html
<!DOCTYPE html>
<html lang="fr">
<head>
<meta charset="utf-8">
<title>Claireval Conseil et Comptes SA – Carte de visite</title>
<link rel="stylesheet" href="https://fonts.googleapis.com/css2?family=Montserrat:wght@500;600&family=Roboto:wght@400;700&display=swap">
<style>
  :root {
    --backdrop: #3b3c40;
    --card: #1d1e22;
    --card-edge: #25262b;
    --accent: #2a9fd8;
    --accent-deep: #1f7fb8;
    --emboss: #2c2d33;
    --text-light: #f2f3f5;
    --text-soft: #d9dbe0;
  }
  * { box-sizing: border-box; margin: 0; padding: 0; }
  html, body {
    width: 799px; height: 1200px; overflow: hidden;
    background: var(--backdrop);
  }
  .sheet { position: relative; width: 799px; height: 1200px; }

  .card {
    position: absolute; left: 110px; width: 580px; height: 330px;
    background: var(--card);
    border: 1px solid var(--card-edge);
    box-shadow: 0 14px 30px rgba(0,0,0,.45);
    overflow: hidden;
  }
  .card--front { top: 120px; }
  .card--back { top: 720px; }

  /* Front */
  .front-band {
    position: absolute; left: 0; right: 0; bottom: 0; height: 12px;
    background: var(--accent);
  }
  .front-name {
    position: absolute; left: 0; right: 0; top: 120px;
    text-align: center;
    font-family: "Montserrat", sans-serif; font-weight: 600;
    font-size: 34px; letter-spacing: 5px; line-height: 1.15;
    color: var(--emboss);
    text-transform: uppercase;
  }

  /* Back */
  .back-band {
    position: absolute; left: 0; top: 0; bottom: 0; width: 58px;
    background: linear-gradient(180deg, var(--accent), var(--accent-deep));
  }
  .brand {
    position: absolute; left: 100px; top: 42px;
    display: flex; align-items: center; gap: 16px;
  }
  .brand-mark { width: 34px; height: 34px; background: var(--accent); }
  .brand-name {
    font-family: "Montserrat", sans-serif; font-weight: 600;
    font-size: 26px; letter-spacing: 3px; line-height: 1.1;
    color: var(--text-light); text-transform: uppercase;
  }
  .person { position: absolute; left: 100px; top: 150px; font-family: "Roboto", sans-serif; }
  .person-name { font-weight: 700; font-size: 23px; color: var(--accent); }
  .person-role { font-size: 13px; color: var(--text-soft); line-height: 1.45; margin-top: 4px; }

  .contacts {
    position: absolute; left: 100px; top: 250px; right: 30px;
    font-family: "Roboto", sans-serif; font-size: 14px; color: var(--text-light);
    list-style: none;
  }
  .contacts-row { display: flex; flex-wrap: wrap; gap: 6px 20px; margin-bottom: 8px; }
  .contact { display: flex; align-items: center; gap: 7px; }
  .contact svg { width: 13px; height: 13px; fill: var(--accent); flex: none; }
</style>
</head>
<body>
<main class="sheet">

  <section class="card card--front" aria-label="Recto">
    <p class="front-name">Claireval<br>Conseil et Comptes</p>
    <div class="front-band"></div>
  </section>

  <section class="card card--back" aria-label="Verso">
    <div class="back-band"></div>

    <div class="brand">
      <span class="brand-mark"></span>
      <span class="brand-name">Claireval<br>Conseil et Comptes</span>
    </div>

    <div class="person">
      <p class="person-name">Tomas Varenholt</p>
      <p class="person-role">Directeur et Fondateur<br>Expert-comptable diplômé</p>
    </div>

    <div class="contacts">
      <div class="contacts-row">
        <span class="contact">
          <svg viewBox="0 0 24 24" aria-hidden="true"><path d="M6.6 10.8a15.2 15.2 0 0 0 6.6 6.6l2.2-2.2c.3-.3.7-.4 1-.2 1.1.4 2.3.6 3.6.6.6 0 1 .4 1 1V20c0 .6-.4 1-1 1A17 17 0 0 1 3 4c0-.6.4-1 1-1h3.5c.6 0 1 .4 1 1 0 1.3.2 2.5.6 3.6.1.3 0 .7-.2 1z"/></svg>
          022 418 57 34
        </span>
        <span class="contact">
          <svg viewBox="0 0 24 24" aria-hidden="true"><path d="M2 5h20v14H2zm2 2v.5l8 5 8-5V7z"/></svg>
          tv@clairevalconseil.ch
        </span>
        <span class="contact">
          <svg viewBox="0 0 24 24" aria-hidden="true"><circle cx="12" cy="12" r="10"/></svg>
          www.clairevalconseil.ch
        </span>
      </div>
      <div class="contacts-row">
        <span class="contact">
          <svg viewBox="0 0 24 24" aria-hidden="true"><path d="M12 2a7 7 0 0 0-7 7c0 5 7 13 7 13s7-8 7-13a7 7 0 0 0-7-7zm0 9.5A2.5 2.5 0 1 1 12 6.5a2.5 2.5 0 0 1 0 5z"/></svg>
          Rue des Vergières 27 1201 Genève
        </span>
      </div>
    </div>
  </section>

</main>
</body>
</html>
```